Label design for outdoor terrace cleaner

We are Marlek Yard Living and searching for a modern, clean but colorful and exciting label packaging design. Our product is Tolvik Patio and is a weedage and terrace cleaner. It is a consumer product for webshops and retail shops, which should stand out by design and colors. We also would like it to be very visibly appealing with a photo.

Label size: 240 mm x 176 mm

Logo: MARLEK (Please adjust to any color you want)
Slogan: YARD LIVING (as part of the logo)

Label text is dutch, if you need any help with that, please ask.

Target Market(s)

Outdoor cleaning, retail market, handy shops, consumer retail market

Industry/Entity Type

Cleaning Product

Colors

Designer to choose colors to be used in the design.

Requirements
Must have
• Original ideas, marketing thoughts, some extra brainstorming for an outstanding and original result including texts, that will have consumers see our product and want to buy it. Smart use of words, photos and colors.
Nice to have
• Bright and visibly appealing colors (should include green, but nothing standard) and photo
Should not have
• Standard, dull appearance

```html
<!DOCTYPE html>
<html lang="nl">
<head>
<meta charset="utf-8">
<title>Marlek Yard Living – Tolvik Patio label</title>
<link rel="stylesheet" href="https://fonts.googleapis.com/css2?family=Poppins:wght@300;400;600;700&family=Saira+Semi+Condensed:wght@300;400&display=block">
<style>
  :root {
    --page: #ffffff;
    --sky: #cfe3ee;
    --sky-deep: #8fb8cc;
    --hills: #7fa58a;
    --meadow: #7ea04e;
    --deck: #b9bcbd;
    --deck-dark: #8f9293;
    --olive: #a9b43e;
    --orange: #e2682c;
    --navy: #1d4f8f;
    --ink: #2b3a55;
    --caption: #111111;
    --panel: rgba(255, 255, 255, 0.55);
    --logo-panel: rgba(240, 240, 232, 0.78);
  }
  html, body {
    margin: 0;
    width: 1131px;
    height: 1200px;
    overflow: hidden;
    background: var(--page);
  }
  .canvas {
    position: relative;
    width: 1131px;
    height: 1200px;
  }
  .sheet {
    position: absolute;
    left: 30px;
    top: 170px;
    width: 1020px;
    height: 840px;
    transform: scale(1.05);
    transform-origin: 0 0;
  }
  .label {
    position: absolute;
    left: 0;
    top: 0;
    width: 1020px;
    height: 748px;
    overflow: hidden;
    font-family: "Poppins", sans-serif;
  }
  .label__photo {
    position: absolute;
    inset: 0;
    background:
      radial-gradient(ellipse 260px 140px at 560px 30px, rgba(255,255,255,0.75), rgba(255,255,255,0) 70%),
      linear-gradient(180deg,
        var(--sky-deep) 0%,
        var(--sky) 22%,
        #b7cdc7 34%,
        var(--hills) 46%,
        var(--meadow) 62%,
        #9aa98e 68%,
        var(--deck) 74%,
        var(--deck-dark) 100%);
  }
  .label__shapes {
    position: absolute;
    inset: 0;
  }
  .brand {
    position: absolute;
    left: 28px;
    top: 80px;
    width: 460px;
    height: 142px;
    border-radius: 12px;
    background: var(--logo-panel);
    display: flex;
    align-items: center;
    justify-content: center;
  }
  .brand__name {
    font-family: "Poppins", sans-serif;
    font-weight: 700;
    font-size: 104px;
    line-height: 1;
    letter-spacing: 2px;
    color: var(--orange);
  }
  .brand__line {
    position: absolute;
    left: 175px;
    top: 238px;
    padding: 0 4px;
    background: var(--logo-panel);
    font-family: "Saira Semi Condensed", sans-serif;
    font-weight: 400;
    font-size: 25px;
    line-height: 30px;
    letter-spacing: 1px;
    word-spacing: 6px;
    color: var(--navy);
  }
  .claims {
    position: absolute;
    left: 120px;
    top: 470px;
    width: 306px;
    margin: 0;
    padding: 0;
    list-style: none;
    text-align: center;
  }
  .claims li {
    height: 43px;
    font-family: "Saira Semi Condensed", sans-serif;
    font-weight: 300;
    font-size: 19px;
    letter-spacing: -0.6px;
    white-space: nowrap;
    color: var(--navy);
  }
  .tagline {
    position: absolute;
    left: 20px;
    top: 694px;
    margin: 0;
    font-weight: 300;
    font-size: 13px;
    line-height: 17px;
    color: var(--ink);
  }
  .info {
    position: absolute;
    border-radius: 10px;
    background: var(--panel);
    padding: 8px 14px 6px;
    box-sizing: border-box;
    font-size: 11.5px;
    line-height: 27px;
    font-weight: 400;
    color: #22262e;
  }
  .info--use { left: 535px; top: 110px; width: 460px; height: 247px; }
  .info--notes { left: 545px; top: 410px; width: 450px; height: 247px; }
  .info h2 {
    margin: 0;
    font-size: 11.5px;
    font-weight: 400;
    line-height: 27px;
  }
  .info ul {
    margin: 0;
    padding: 0;
    list-style: none;
  }
  .info li::before { content: "•  "; }
  .info--notes li { text-align: justify; }
  .caption {
    position: absolute;
    top: 770px;
    font-family: "Poppins", sans-serif;
    font-size: 24px;
    font-weight: 400;
    color: var(--caption);
    transform: translateX(-50%);
  }
  .caption--front { left: 252px; }
  .caption--back { left: 758px; }
</style>
</head>
<body>
<div class="canvas">
  <div class="sheet">
    <section class="label" aria-label="Tolvik Patio label, front and back">
      <div class="label__photo" role="img" aria-label="Photo of a wooden terrace deck overlooking green hills under a bright sky"></div>

      <svg class="label__shapes" width="1020" height="748" viewBox="0 0 1020 748" aria-hidden="true">
        <path d="M540 0 C 600 40, 700 30, 800 25 C 900 20, 990 50, 1020 122 L 1020 0 Z" fill="var(--olive)"/>
        <path d="M0 595 C 80 630, 120 690, 250 690 C 380 690, 430 620, 500 650 C 560 680, 575 730, 590 748 L 0 748 Z" fill="var(--olive)"/>
      </svg>

      <div class="brand"><span class="brand__name">MARLEK</span></div>
      <div class="brand__line">YARD LIVING</div>

      <ul class="claims">
        <li>Zonder glyfosfaat</li>
        <li>Concentraat zonder giftige stoffen</li>
        <li>Resultaat binnen enkele uren</li>
        <li>Voor paden en terrassen</li>
      </ul>

      <p class="tagline">Groen terras.<br>De must-have reiniger voor alle type terrassen, voor ieder huishouden.</p>

      <div class="info info--use">
        <h2>Useinstructions:</h2>
        <ul>
          <li>Verdun het tot een 25% oplossing (bijv. 1 liter Tolvik Patio en 3 liter water).</li>
          <li>Besproei of begiet het terras met deze oplossing. 2 liter per 10 m2. (1 liter Tolvik Patio is dus voldoende voor ca. 20 m2 terras).</li>
          <li>Niet toepassen in de volle zon en als er binnen enkele uren veel neerslag wordt verwacht.</li>
          <li>Eventueel na enkele dagen het los gekomen vuil van het terras vegen of spuiten.</li>
        </ul>
      </div>

      <div class="info info--notes">
        <h2>Notes:</h2>
        <ul>
          <li>Op zeer hardnekkige vervuiling kan het product eventueel onverdund worden toegepast.</li>
          <li>Tolvik Patio tast bij toepassing conform de gebruiksaanwijzing gangbare buiten (natuur)steen, tegels en hout niet aan.</li>
          <li>Voorkom dat reinigingsproducten in contact komen met gewassen en/of direct in het oppervlaktewater terecht komen.</li>
          <li>Neem veiligheidsmaatregel in acht bij het werken met het onverdunde product.</li>
        </ul>
      </div>
    </section>

    <span class="caption caption--front">Front</span>
    <span class="caption caption--back">Back</span>
  </div>
</div>
</body>
</html>
```